Harborline Auto LLC

Car Dealer Customer Service
Address: 2874 Cresthaven Road, Shelbyville, TN 37162
web: www.harborlineautoxq.net
email: harborlineautoxq@mailnest.example
Phone: (931) 555-0148
Phone: (629) 555-0173

```html
<!DOCTYPE html>
<html lang="en">
<head>
<meta charset="utf-8">
<title>Harborline Auto – Business Card</title>
<link rel="stylesheet" href="https://fonts.googleapis.com/css2?family=Poppins:wght@400;500;700&display=swap">
<style>
  :root {
    --backdrop: #2b2b2b;
    --card: #f1f1f1;
    --blue: #1f7bb0;
    --blue-deep: #175f8c;
    --gold: #e0a93b;
    --ink: #222222;
  }
  * { margin: 0; padding: 0; box-sizing: border-box; }
  html, body { width: 1200px; height: 1138px; overflow: hidden; }
  body {
    background: var(--backdrop);
    font-family: "Poppins", sans-serif;
    position: relative;
  }
  .card {
    position: absolute;
    width: 620px;
    height: 374px;
    background: var(--card);
    border-radius: 16px;
    overflow: hidden;
  }
  .card-front { left: 274px; top: 186px; }
  .card-back { left: 276px; top: 608px; }

  /* front */
  .front-mark {
    position: absolute;
    left: 50%;
    top: 92px;
    width: 64px;
    height: 64px;
    margin-left: -32px;
    border-radius: 50%;
    background: var(--blue);
  }
  .front-name {
    position: absolute;
    left: 0; right: 0;
    top: 176px;
    text-align: center;
    color: var(--blue-deep);
    font-weight: 700;
    font-size: 30px;
    letter-spacing: 0.5px;
  }
  .front-web {
    position: absolute;
    left: 0; right: 0;
    top: 320px;
    display: flex;
    justify-content: center;
    align-items: center;
    gap: 22px;
    font-size: 15px;
    color: var(--ink);
  }
  .front-web .rule { width: 54px; height: 2px; background: var(--gold); }
  .front-band {
    position: absolute;
    left: 0; right: 0; bottom: 0;
    height: 18px;
    display: flex;
  }
  .front-band .band-blue { flex: 1; background: var(--blue); }
  .front-band .band-gold { flex: 1; background: var(--gold); }

  /* back */
  .back-disc {
    position: absolute;
    left: -100px;
    top: 2px;
    width: 380px;
    height: 380px;
    border-radius: 50%;
    background: var(--blue);
  }
  .back-info {
    position: absolute;
    right: 26px;
    top: 38px;
    text-align: right;
  }
  .back-company {
    color: var(--blue-deep);
    font-weight: 700;
    font-size: 30px;
    letter-spacing: 0.5px;
    line-height: 1.2;
  }
  .person { margin-top: 58px; }
  .person-name { color: var(--blue-deep); font-weight: 700; font-size: 23px; line-height: 1.2; }
  .person-role { font-size: 16px; color: var(--ink); margin-top: 2px; }
  .contacts { margin-top: 30px; list-style: none; }
  .contacts li {
    display: flex;
    justify-content: flex-end;
    align-items: center;
    gap: 10px;
    font-size: 16px;
    line-height: 22px;
    color: var(--ink);
  }
  .contacts li.phone { font-weight: 700; color: var(--blue-deep); letter-spacing: 0.5px; }
  .contacts svg { width: 15px; height: 15px; fill: var(--gold); flex: none; }
  .contacts li.address { padding-right: 0; margin-top: 4px; }
</style>
</head>
<body>

<section class="card card-front" aria-label="Card front">
  <div class="front-mark" aria-hidden="true"></div>
  <h1 class="front-name">HARBORLINE AUTO</h1>
  <div class="front-web">
    <span class="rule"></span>
    <span>www.harborlineautoxq.net</span>
    <span class="rule"></span>
  </div>
  <div class="front-band"><span class="band-blue"></span><span class="band-gold"></span></div>
</section>

<section class="card card-back" aria-label="Card back">
  <div class="back-disc" aria-hidden="true"></div>
  <div class="back-info">
    <h2 class="back-company">HARBORLINE AUTO</h2>
    <div class="person">
      <p class="person-name">Dorian Vell</p>
      <p class="person-role">Managing Director</p>
    </div>
    <ul class="contacts">
      <li class="phone">931-555-0148
        <svg viewBox="0 0 24 24" aria-hidden="true"><path d="M6.6 10.8a15.1 15.1 0 0 0 6.6 6.6l2.2-2.2c.3-.3.7-.4 1-.2 1.1.4 2.3.6 3.6.6.6 0 1 .4 1 1V20c0 .6-.4 1-1 1A17 17 0 0 1 3 4c0-.6.4-1 1-1h3.5c.6 0 1 .4 1 1 0 1.3.2 2.5.6 3.6.1.3 0 .7-.2 1z"/></svg>
      </li>
      <li class="phone">629-555-0173
        <svg viewBox="0 0 24 24" aria-hidden="true"><path d="M6.6 10.8a15.1 15.1 0 0 0 6.6 6.6l2.2-2.2c.3-.3.7-.4 1-.2 1.1.4 2.3.6 3.6.6.6 0 1 .4 1 1V20c0 .6-.4 1-1 1A17 17 0 0 1 3 4c0-.6.4-1 1-1h3.5c.6 0 1 .4 1 1 0 1.3.2 2.5.6 3.6.1.3 0 .7-.2 1z"/></svg>
      </li>
      <li>www.harborlineautoxq.net
        <svg viewBox="0 0 24 24" aria-hidden="true"><path d="M2 5h20v14H2z M3.5 6.5 12 13l8.5-6.5" fill="none" stroke="#e0a93b" stroke-width="2"/></svg>
      </li>
      <li>harborlineautoxq@mailnest.example
        <svg viewBox="0 0 24 24" aria-hidden="true"><circle cx="12" cy="12" r="9" fill="none" stroke="#e0a93b" stroke-width="2"/><path d="M3 12h18M12 3c3 3 3 15 0 18M12 3c-3 3-3 15 0 18" fill="none" stroke="#e0a93b" stroke-width="1.6"/></svg>
      </li>
      <li class="address">2874 Cresthaven Road, Shelbyville, TN 37162</li>
    </ul>
  </div>
</section>

</body>
</html>
```